Natural Light/Organic/Documentary Photography Business

I like a simple, approachable, feminine, earthy/organic feel. Earth/neutral tones, nothing too loud or obnoxious. I like the watercolor look. I don't want anything too trendy or something I'll get tired of after a couple months. As far as colors, I am much more a fan of cream/taupe/blue/green...not a fan of pink or purple at all.

Target Market(s)

Weddings & Families

Industry/Entity Type

Wedding Photography

Contact Information for Business Card

website, email, phone number

Font styles to use
Other font styles liked:
• Horizontes, Gotham

Colors

Designer to choose colors to be used in the design.

Requirements
Must have
• Website: www.mirelhatchway.com
• Phone: 418.629.5073
• Email: mirel@mirelhatchway.com
Nice to have
• I like the watercolor look but its not necessary. I like simple/earthy tones. Nothing too loud or distracting. Simple & feminine without being too girly. I like an approachable/soft feel.
• Instagram: www.snapfolio.net/mirelhatchwayphotography/
Should not have
• NO loud colors or design or pattern. I do not want a photo of a camera or lens or anything cheesy like that.

```html
<!DOCTYPE html>
<html lang="en">
<head>
<meta charset="utf-8">
<title>Mirel Hatchway Photography – Business Card</title>
<link href="https://fonts.googleapis.com/css2?family=Open+Sans:wght@400&display=swap" rel="stylesheet">
<style>
  :root {
    --backdrop: #b3b3b3;
    --card-white: #ffffff;
    --taupe: #8e8075;
    --taupe-icon: #8a7a6e;
    --taupe-light: #a99d94;
    --ink: #2a2a2a;
    --on-taupe: #ffffff;
  }
  * { margin: 0; padding: 0; box-sizing: border-box; }
  html, body {
    width: 1200px; height: 802px; overflow: hidden;
    background: var(--backdrop);
    font-family: "Open Sans", Arial, sans-serif;
  }
  .canvas { position: relative; width: 1200px; height: 802px; }
  .card {
    position: absolute; top: 274px;
    width: 443px; height: 265px;
  }
  .card--front { left: 136px; background: var(--card-white); }
  .card--back { left: 624px; background: var(--taupe); }

  .brand { position: absolute; text-align: center; white-space: nowrap; }
  .brand-name { font-weight: 400; letter-spacing: 1px; line-height: 1.1; }
  .brand-tag { font-weight: 400; text-transform: uppercase; }

  .card--front .brand { left: 33px; top: 42px; }
  .card--front .brand-name { font-size: 27px; color: var(--taupe); }
  .card--front .brand-tag {
    font-size: 6px; letter-spacing: 3px; color: var(--taupe-light); margin-top: 4px;
  }

  .card--back .brand { left: 0; right: 0; top: 92px; }
  .card--back .brand-name { font-size: 36px; color: var(--on-taupe); }
  .card--back .brand-tag {
    font-size: 8px; letter-spacing: 4px; color: var(--on-taupe); margin-top: 4px;
  }

  .contact-list {
    position: absolute; left: 33px; top: 182px;
    list-style: none; font-size: 13px; line-height: 16px; color: var(--ink);
  }
  .contact-list li { display: flex; align-items: center; gap: 4px; }
  .contact-icon { width: 10px; height: 10px; flex: none; }

  .social-rule {
    position: absolute; left: 64px; top: 184px; width: 311px; height: 18px;
  }
  .social-url {
    position: absolute; left: 0; right: 0; top: 210px;
    text-align: center; font-size: 13px; color: var(--on-taupe);
  }
</style>
</head>
<body>
<main class="canvas">
  <section class="card card--front" aria-label="Card front">
    <div class="brand">
      <p class="brand-name">Mirel Hatchway</p>
      <p class="brand-tag">Photography</p>
    </div>
    <ul class="contact-list">
      <li>
        <svg class="contact-icon" viewBox="0 0 10 10" aria-hidden="true">
          <path d="M1 3.2 Q5 0.6 9 3.2 L8.2 4.6 L6.6 4 L6.6 3.2 Q5 2.6 3.4 3.2 L3.4 4 L1.8 4.6 Z" fill="var(--taupe-icon)"/>
          <rect x="2.2" y="5" width="5.6" height="3.6" rx="0.6" fill="var(--taupe-icon)"/>
        </svg>
        418.629.5073
      </li>
      <li>
        <svg class="contact-icon" viewBox="0 0 10 10" aria-hidden="true">
          <rect x="1" y="2.2" width="8" height="5.8" fill="var(--taupe-icon)"/>
          <path d="M1 2.4 L5 5.6 L9 2.4" fill="none" stroke="#fff" stroke-width="0.8"/>
        </svg>
        mirel@mirelhatchway.com
      </li>
      <li>
        <svg class="contact-icon" viewBox="0 0 10 10" aria-hidden="true">
          <circle cx="5" cy="5" r="4.2" fill="var(--taupe-icon)"/>
          <path d="M2.6 3.4 Q4 2.6 4.6 4 Q3.6 5.2 4.4 7 Q3 6.6 2.6 3.4 Z M5.8 2 Q7.6 3 7.2 5.2 Q6.2 4.6 5.8 2 Z" fill="#fff" opacity="0.85"/>
        </svg>
        www.mirelhatchway.com
      </li>
    </ul>
  </section>

  <section class="card card--back" aria-label="Card back">
    <div class="brand">
      <p class="brand-name">Mirel Hatchway</p>
      <p class="brand-tag">Photography</p>
    </div>
    <svg class="social-rule" viewBox="0 0 311 18" aria-hidden="true">
      <line x1="0" y1="9" x2="142" y2="9" stroke="var(--on-taupe)" stroke-width="1"/>
      <circle cx="155.5" cy="9" r="8" fill="var(--on-taupe)"/>
      <line x1="169" y1="9" x2="311" y2="9" stroke="var(--on-taupe)" stroke-width="1"/>
    </svg>
    <p class="social-url">www.snapfolio.net/mirelhatchwayphotography/</p>
  </section>
</main>
</body>
</html>
```